The design should look similar to the uploaded example to accommodate the information needed for a business card template. I would like to see the colors orange and charcoal grey incorporated along with the logo.The following should be on the back of the card SPECIALIZING IN NEW AND USED TIRES & WHEELS FOR:- Loaders- Skid Steers- Telehandlers- Boom Lifts- Forklifs and moreELIMINATING DOWNTIMEWheel Exchange Program for New & Used Foam Filled and Solid Rubber TiresSPECIALTY SERVICES- Foam Filling Tires- Largest Tire Press in SE- ONSITE Forklift Tire Press- Boom Truck Services - Rubber Tracks

Target Market(s)

New and Existing Customers

Industry/Entity Type

Business

Contact Information for Business Card

NAMEHEAVY DUTY TIRE, LLC8470 Belvedere RoadWest Palm Beach, FL 33411P: 844-HD-TIRESF: 561-431-6469C:E: W: WWW.GRANITERIMSUPPLY-EXAMPLE.COM

Font styles to use
Sans Serif

Colors
f37122
333333

Requirements
Must have
• The logo and the information indicated for the backside of the card
Nice to have
• Keep the orange and charcoal grey colors

```html
<!DOCTYPE html>
<html lang="en">
<head>
<meta charset="utf-8">
<title>Granite Rim Supply – Business Card</title>
<link rel="stylesheet" href="https://fonts.googleapis.com/css2?family=Alfa+Slab+One&family=Open+Sans:wght@400;600&display=swap">
<style>
  :root {
    --orange: #f48a43;
    --charcoal: #3b4648;
    --ink: #454f51;
    --backdrop: #7d7d7d;
    --white: #ffffff;
    --sky: #7fa9d6;
    --mist: #e9edf1;
    --rubber: #a9adb0;
  }
  * { margin: 0; padding: 0; box-sizing: border-box; }
  html, body { width: 992px; height: 1200px; overflow: hidden; }
  body { background: var(--backdrop); font-family: "Open Sans", sans-serif; position: relative; }

  .card { position: absolute; left: 68px; width: 869px; height: 495px; overflow: hidden; }
  .card-front { top: 67px; }
  .card-back { top: 627px; background: var(--white); }
  .card-art { position: absolute; inset: 0; }

  .company-name {
    position: absolute; right: 38px; top: 50px;
    font-family: "Alfa Slab One", serif; font-size: 28px; letter-spacing: 1px;
    color: var(--charcoal);
  }
  .address {
    position: absolute; right: 37px; top: 140px; text-align: right;
    font-size: 26px; line-height: 34px; color: var(--ink);
  }
  .contact-list { position: absolute; right: 37px; top: 291px; list-style: none; }
  .contact-list li {
    display: flex; align-items: center; justify-content: flex-end;
    height: 33px; font-size: 23px; color: var(--white);
  }
  .contact-list svg { width: 18px; height: 18px; margin-left: 20px; flex: none; }

  .back-photo { position: absolute; inset: 0; background: linear-gradient(180deg, #eef1f4 0%, #f6f7f8 30%, #e4e6e8 60%, #f2f3f4 100%); }
  .services-heading {
    position: absolute; left: 124px; top: 117px;
    font-size: 32px; color: var(--charcoal); letter-spacing: 0.5px;
  }
  .services-heading .accent { color: var(--orange); }
  .rule { position: absolute; top: 139px; height: 2px; background: var(--charcoal); }
  .rule-left { left: 0; width: 112px; }
  .rule-right { left: 464px; width: 114px; }

  .service-list { position: absolute; left: 82px; top: 229px; list-style: none; }
  .service-list li {
    display: flex; align-items: center; height: 43.5px;
    font-size: 26px; color: var(--charcoal);
  }
  .service-list li::before {
    content: ""; width: 14px; height: 14px; border-radius: 50%;
    border: 4px solid var(--orange); margin-right: 30px; flex: none;
  }

  .brand-mark { position: absolute; left: 596px; top: 95px; display: flex; align-items: center; }
  .brand-dot { width: 86px; height: 86px; border-radius: 50%; background: var(--orange); flex: none; margin-right: 16px; }
  .brand-name { font-size: 28px; font-weight: 600; line-height: 34px; color: var(--charcoal); }

  .badge { position: absolute; }
  .badge-association { left: 530px; top: 340px; width: 164px; height: 120px; border-radius: 6px; background: #d6dbe6; }
  .badge-retread { left: 700px; top: 343px; width: 118px; height: 118px; border-radius: 50%; background: var(--white); border: 3px solid var(--charcoal); }
</style>
</head>
<body>

<section class="card card-front">
  <svg class="card-art" viewBox="0 0 869 495" width="869" height="495">
    <defs>
      <linearGradient id="tread-photo" x1="0" y1="0" x2="0" y2="1">
        <stop offset="0" stop-color="#dfe8f2"/>
        <stop offset="0.3" stop-color="#8fb4dc"/>
        <stop offset="0.45" stop-color="#9aa0a5"/>
        <stop offset="1" stop-color="#c6c9cc"/>
      </linearGradient>
    </defs>
    <rect width="869" height="495" fill="url(#tread-photo)" role="img" aria-label="Close-up photo of a heavy tire tread against a cloudy sky"/>
    <path d="M290,0 Q405,255 280,495 L869,495 L869,0 Z" fill="var(--charcoal)"/>
    <path d="M308,0 L869,0 L869,255 L364,255 Q352,110 308,0 Z" fill="var(--orange)"/>
  </svg>

  <h1 class="company-name">GRANITE RIM SUPPLY LLC</h1>
  <p class="address">5126 Marston Lane<br>West Palm Beach, FL 33411</p>

  <ul class="contact-list">
    <li>0412 307 918
      <svg viewBox="0 0 18 18"><rect width="18" height="18" rx="2" fill="#fff"/><rect x="6" y="3" width="6" height="12" rx="1" fill="none" stroke="#3b4648" stroke-width="1.5"/></svg></li>
    <li>844-GR-WHEEL
      <svg viewBox="0 0 18 18"><rect width="18" height="18" rx="2" fill="#fff"/><path d="M5,4 L8,4 L8.5,7 L7,8 Q8,11 10,12 L11,10.5 L14,11 L14,14 Q7,14 4,7 Z" fill="#3b4648"/></svg></li>
    <li>561-278-9053
      <svg viewBox="0 0 18 18"><rect width="18" height="18" rx="2" fill="#fff"/><rect x="4" y="7" width="10" height="6" fill="#3b4648"/><rect x="6" y="4" width="6" height="3" fill="#3b4648"/></svg></li>
    <li>info@graniterimsupply-example.com
      <svg viewBox="0 0 18 18"><rect width="18" height="18" rx="2" fill="#fff"/><rect x="3.5" y="5" width="11" height="8" fill="#3b4648"/><path d="M3.5,5 L9,10 L14.5,5" fill="none" stroke="#fff" stroke-width="1.2"/></svg></li>
    <li>www.graniterimsupply-example.com
      <svg viewBox="0 0 18 18"><rect width="18" height="18" rx="2" fill="#fff"/><circle cx="9" cy="9" r="5.5" fill="#3b4648"/><path d="M3.5,9 H14.5 M9,3.5 V14.5" stroke="#fff" stroke-width="1"/></svg></li>
  </ul>
</section>

<section class="card card-back">
  <div class="back-photo" role="img" aria-label="Faded photo of a tire tread under a pale sky"></div>

  <span class="rule rule-left"></span>
  <h2 class="services-heading"><span class="accent">SPECIALTY</span> SERVICES</h2>
  <span class="rule rule-right"></span>

  <ul class="service-list">
    <li>Foam Filling Tires</li>
    <li>Largest Tire Press in SE</li>
    <li>ONSITE Forklift Tire Press</li>
    <li>Boom Truck Services</li>
    <li>Rubber Tracks</li>
  </ul>

  <div class="brand-mark">
    <span class="brand-dot"></span>
    <span class="brand-name">GRANITE RIM<br>SUPPLY</span>
  </div>

  <span class="badge badge-association" role="img" aria-label="Rental association membership badge"></span>
  <span class="badge badge-retread" role="img" aria-label="Retread association membership badge"></span>
</section>

</body>
</html>
```